Software Company Business Card Design

We are looking for a business card design for a software, messaging & IT services company based in Australia.

Heron Collective is the holding company for 3 brands all offering technology based business solutions; Heron, Velotix & Briefloop. Brand Identity = Friendly, Professional, Viable, Vibrant, Creative

We want our business card to reflect that we are an innovative market leader. The design should be clean, professional and original.

This design will be used for all 3 brands.

More information about our company can be found at: www.heroncollective-example.com.au
www.velotix-example.com.au

Details we would like on the card:

Firstname Lastname
Position
Level 14, 62 Dunmore St
North Sydney
NSW 2060
Phone: +61 2 8364 7200
Fax: +61 2 8364 7219
www.heroncollective-example.com.au

Target Market(s)

Our business cards are given to B2B and industry professionals.

Industry/Entity Type

Business

Requirements
Must have
• The Business Card must include the same colours as the logo.
Nice to have
• We would like it to me double sided.

```html
<!DOCTYPE html>
<html lang="en">
<head>
<meta charset="utf-8">
<title>Heron Collective – Business Card</title>
<link rel="stylesheet" href="https://fonts.googleapis.com/css2?family=Outfit:wght@400;500;600&family=Arimo:wght@400;700&display=swap">
<style>
  :root {
    --stage: #121212;
    --brand-crimson: #b3123e;
    --brand-lavender: #9495bb;
    --label-lavender: #7c7da8;
    --card-white: #f6f6f6;
    --grey-light: #f4f4f4;
    --grey-edge: #a3a3a3;
    --ink-dark: #3c3c3c;
    --ink-mid: #555555;
  }
  * { margin: 0; padding: 0; box-sizing: border-box; }
  html, body {
    width: 1200px; height: 996px; overflow: hidden;
    background: var(--stage);
  }
  .canvas { position: relative; width: 1200px; height: 996px; }
  .card {
    position: absolute; top: 205px;
    width: 562px; height: 337px;
  }
  .card--front {
    left: 27px;
    background: radial-gradient(ellipse 300px 230px at 47% 45%, var(--grey-light) 0%, #e6e6e6 35%, #c4c4c4 70%, var(--grey-edge) 100%);
  }
  .card--back { left: 618px; background: var(--card-white); }

  .brand {
    position: absolute; left: 58px; top: 128px;
    display: flex; align-items: center; gap: 16px;
  }
  .brand__dot {
    width: 34px; height: 34px; border-radius: 50%;
    background: var(--brand-lavender);
  }
  .brand__name {
    font-family: "Outfit", sans-serif; font-weight: 500;
    font-size: 50px; letter-spacing: -0.5px;
    color: var(--brand-crimson); line-height: 1;
  }

  .holder { position: absolute; left: 49px; top: 66px; color: var(--ink-dark); }
  .holder__name {
    font-family: "Outfit", sans-serif; font-size: 30px; line-height: 1;
    letter-spacing: -0.3px;
  }
  .holder__first { font-weight: 600; }
  .holder__last { font-weight: 400; }
  .holder__position {
    font-family: "Outfit", sans-serif; font-size: 22px; font-weight: 400;
    color: var(--ink-mid); margin-top: 1px; line-height: 1;
  }

  .contact {
    position: absolute; left: 49px; top: 159px;
    font-family: "Arimo", sans-serif; font-size: 17px; line-height: 21.5px;
    color: var(--ink-mid); list-style: none;
  }
  .contact__label { color: var(--label-lavender); }
  .contact__phone { font-weight: 700; color: var(--ink-dark); }

  .web {
    position: absolute; left: 49px; top: 260px;
    font-family: "Arimo", sans-serif; font-size: 16px; font-weight: 700;
    letter-spacing: 3.2px; color: var(--ink-mid);
  }
</style>
</head>
<body>
<main class="canvas">
  <section class="card card--front" aria-label="Card front">
    <div class="brand">
      <span class="brand__dot"></span>
      <span class="brand__name">Heron Collective</span>
    </div>
  </section>

  <section class="card card--back" aria-label="Card back">
    <div class="holder">
      <p class="holder__name"><span class="holder__first">Firstname</span> <span class="holder__last">Lastname</span></p>
      <p class="holder__position">position</p>
    </div>
    <ul class="contact">
      <li><span class="contact__label">P:</span> <span class="contact__phone">+61 2 8364 7200</span></li>
      <li><span class="contact__label">F:</span> +61 2 8364 7219</li>
      <li><span class="contact__label">A:</span> Level 14, 62 Dunmore St North</li>
      <li>Sydney NSW 2060</li>
    </ul>
    <p class="web">www.heroncollective-example.com.au</p>
  </section>
</main>
</body>
</html>
```